Design a New Business Card for Our Company

We are looking for fresh, unique, and a modern business card that reflects our roots as digital marketing agency focused on SEM.

Industry/Entity Type

Marketing

Contact Information for Business Card

looking for very unique out of the box designs. clean and modern that compliments our logo

Requirements
Must have
• colors should match our logo
• Front should have name, address, email, and phone/fax of the person, phone/fax are the same number
• back should have our url

```html
<!DOCTYPE html>
<html lang="en">
<head>
<meta charset="utf-8">
<title>Brightway Solutions – Business Card</title>
<link rel="stylesheet" href="https://fonts.googleapis.com/css2?family=Open+Sans:wght@400;600;700&family=Montserrat:wght@800&display=swap">
<style>
  :root {
    --backdrop: #d9d9d9;
    --brand-blue: #114b96;
    --sky-blue: #5e98d2;
    --ink-black: #000000;
    --stripe-grey: #b9b9b9;
    --paper-white: #ffffff;
  }
  * { box-sizing: border-box; margin: 0; padding: 0; }
  html, body {
    width: 1200px; height: 900px; overflow: hidden;
    background: var(--backdrop);
    font-family: "Open Sans", sans-serif;
  }
  .canvas { position: relative; width: 1200px; height: 900px; }

  /* Back of card */
  .card-back {
    position: absolute; left: 390px; top: 50px;
    width: 620px; height: 354px;
    background: var(--brand-blue);
    box-shadow: 0 4px 12px rgba(0,0,0,.25);
    display: flex; flex-direction: column; align-items: center; justify-content: center;
    color: var(--paper-white);
  }
  .brand-lockup { display: flex; align-items: center; gap: 16px; }
  .brand-dot { width: 44px; height: 44px; border-radius: 50%; background: var(--paper-white); }
  .brand-name {
    font-family: "Montserrat", sans-serif; font-weight: 800;
    font-size: 44px; letter-spacing: -0.5px; color: var(--paper-white);
  }
  .website { margin-top: 38px; font-size: 15px; font-weight: 700; }

  /* Front of card */
  .card-front {
    position: absolute; left: 150px; top: 430px;
    width: 760px; height: 434px;
    background: var(--sky-blue);
    box-shadow: 0 4px 12px rgba(0,0,0,.3);
    overflow: hidden;
  }
  .card-front .swoosh { position: absolute; inset: 0; }
  .contact {
    position: absolute; right: 38px; top: 110px;
    text-align: right; color: var(--paper-white);
  }
  .person-name { font-size: 24px; font-weight: 700; line-height: 1.1; }
  .person-role { font-size: 18px; margin-bottom: 34px; }
  .contact-line {
    display: flex; justify-content: flex-end; align-items: center; gap: 10px;
    font-size: 19px; line-height: 1.3;
  }
  .contact-line svg { width: 16px; height: 16px; fill: var(--paper-white); flex: none; }
  .spacer { height: 18px; }
  .address-text { text-align: right; }
</style>
</head>
<body>
<div class="canvas">

  <section class="card-back">
    <div class="brand-lockup">
      <span class="brand-dot"></span>
      <span class="brand-name">Brightway Solutions</span>
    </div>
    <div class="website">www.brightwaysolutions.com</div>
  </section>

  <section class="card-front">
    <svg class="swoosh" viewBox="0 0 760 434" preserveAspectRatio="none">
      <path d="M0 0 H430 C470 60 470 260 300 434 H0 Z" fill="var(--stripe-grey)"/>
      <path d="M0 0 H410 C455 70 440 260 270 434 H0 Z" fill="var(--ink-black)"/>
      <circle cx="190" cy="200" r="60" fill="var(--stripe-grey)"/>
    </svg>

    <div class="contact">
      <div class="person-name">Daniel Brooks</div>
      <div class="person-role">Managing Director</div>

      <div class="contact-line">123.456.7890
        <svg viewBox="0 0 16 16"><path d="M3 2h3l1 4-2 1a8 8 0 0 0 4 4l1-2 4 1v3a1 1 0 0 1-1 1A13 13 0 0 1 2 3a1 1 0 0 1 1-1z"/></svg>
      </div>
      <div class="contact-line">123.456.7890
        <svg viewBox="0 0 16 16"><path d="M4 1h7v4H4zM2 6h12v8H2zm3 2v1h2V8zm4 0v1h2V8zm-4 3v1h2v-1zm4 0v1h2v-1z"/></svg>
      </div>
      <div class="contact-line">info@youremail.com
        <svg viewBox="0 0 16 16"><path d="M1 3h14v10H1zm1 1v1l6 4 6-4V4z"/></svg>
      </div>

      <div class="spacer"></div>
      <div class="contact-line">1234, Address Goes Here
        <svg viewBox="0 0 16 16"><path d="M8 1a5 5 0 0 1 5 5c0 4-5 9-5 9S3 10 3 6a5 5 0 0 1 5-5zm0 3a2 2 0 1 0 0 4 2 2 0 0 0 0-4z"/></svg>
      </div>
      <div class="contact-line address-text" style="padding-right:26px">Country Name, 123456</div>
    </div>
  </section>

</div>
</body>
</html>
```